Business Card for Vorla Parts Wholesale supplier

Hi There! I need a new business card for our company. We are specialized in selling Vorla parts, mostly we sell new LCD screens for Zelnar and Drelks. I would like to see that back in the design.

You can find the colors and logo's on our website: www.hartuvo.nl

Industry/Entity Type

Business

Contact Information for Business Card

My Details:
Tobias Lindqvist

Phone: 0031687203316
E-mail: Tobias@hartuvo.nl

Slogan: "Because Quality Matters"

Font styles to use
Sans Serif

Colors

Designer to choose colors to be used in the design.

Requirements
Must have
• A Black backside with the Hartuvo logo on it. The front side should be clean with only my contact details.
• But I'm also open for something really different or awesome!
Nice to have
• Remember that we are in the parts & repairing industry, So i'll be handing those business cards mainly to repair companies. Maybe you can do something with that thought :)

```html
<!DOCTYPE html>
<html lang="en">
<head>
<meta charset="utf-8">
<title>Hartuvo Business Card</title>
<link rel="stylesheet" href="https://fonts.googleapis.com/css2?family=Oswald:wght@500&family=Work+Sans:wght@400;500;600&display=swap">
<style>
  :root {
    --stage: #1c1c1c;
    --card-black: #0e0e0e;
    --card-white: #ffffff;
    --orange: #f07020;
    --ink: #333333;
    --ink-soft: #444444;
  }
  * { margin: 0; padding: 0; box-sizing: border-box; }
  html, body { width: 1200px; height: 1000px; overflow: hidden; }
  body {
    background: var(--stage);
    font-family: "Work Sans", Arial, sans-serif;
    display: flex;
    flex-direction: column;
    align-items: center;
    justify-content: center;
    gap: 56px;
  }
  .card {
    width: 640px;
    height: 370px;
    border-radius: 18px;
    position: relative;
    overflow: hidden;
  }
  .card-back {
    background: var(--card-black);
    display: flex;
    align-items: center;
    justify-content: center;
  }
  .brand {
    display: flex;
    align-items: center;
    gap: 14px;
  }
  .brand-dot {
    border-radius: 50%;
    background: var(--orange);
  }
  .brand-name {
    font-family: "Work Sans", Arial, sans-serif;
    font-weight: 600;
    letter-spacing: 1px;
    line-height: 1;
  }
  .card-back .brand-dot { width: 54px; height: 54px; }
  .card-back .brand-name { color: #ffffff; font-size: 60px; }

  .card-front { background: var(--card-white); }
  .edge-tab {
    position: absolute;
    left: -14px;
    top: 30px;
    width: 28px;
    height: 42px;
    border-radius: 14px;
    background: var(--orange);
  }
  .holder-name {
    position: absolute;
    left: 44px;
    top: 30px;
    font-family: "Oswald", "Arial Narrow", sans-serif;
    font-weight: 500;
    font-size: 28px;
    letter-spacing: 0.5px;
    color: var(--ink);
    text-transform: uppercase;
  }
  .holder-name .surname { color: var(--orange); }
  .card-front .brand {
    position: absolute;
    right: 56px;
    top: 186px;
  }
  .card-front .brand-dot { width: 40px; height: 40px; }
  .card-front .brand-name { color: #111111; font-size: 44px; }
  .contact-list {
    position: absolute;
    left: 44px;
    top: 226px;
    list-style: none;
    font-size: 15px;
    color: var(--ink-soft);
    letter-spacing: 0.6px;
  }
  .contact-list li {
    display: flex;
    align-items: center;
    gap: 12px;
    height: 22px;
  }
  .contact-list svg { width: 12px; height: 12px; fill: var(--orange); }
  .contact-list .accent { color: var(--orange); }
  .slogan-band {
    position: absolute;
    left: 0;
    right: 0;
    bottom: 0;
    height: 64px;
    background: linear-gradient(var(--orange) 0 26px, var(--card-white) 26px 29px, var(--orange) 29px);
    display: flex;
    align-items: flex-end;
    justify-content: center;
    padding-bottom: 8px;
    color: #ffffff;
    font-size: 15px;
    font-weight: 500;
    letter-spacing: 1.2px;
  }
  .slogan-band {
    background: var(--orange);
    align-items: center;
    padding-bottom: 0;
  }
</style>
</head>
<body>
  <section class="card card-back" aria-label="Card back">
    <div class="brand">
      <span class="brand-dot"></span>
      <span class="brand-name">hartuvo</span>
    </div>
  </section>

  <section class="card card-front" aria-label="Card front">
    <span class="edge-tab"></span>
    <h1 class="holder-name">Tobias <span class="surname">Lindqvist</span></h1>

    <div class="brand">
      <span class="brand-dot"></span>
      <span class="brand-name">hartuvo</span>
    </div>

    <ul class="contact-list">
      <li>
        <svg viewBox="0 0 24 24" aria-hidden="true"><path d="M6.6 10.8a15.1 15.1 0 0 0 6.6 6.6l2.2-2.2c.3-.3.7-.4 1-.2 1.1.4 2.3.6 3.6.6.6 0 1 .4 1 1V20c0 .6-.4 1-1 1A17 17 0 0 1 3 4c0-.6.4-1 1-1h3.5c.6 0 1 .4 1 1 0 1.3.2 2.5.6 3.6.1.3 0 .7-.2 1z"/></svg>
        0031687203316
      </li>
      <li>
        <svg viewBox="0 0 24 24" aria-hidden="true"><path d="M2 5h20v14H2z M2 5l10 8 10-8" /><path d="M2 5l10 8 10-8" fill="#fff"/></svg>
        Tobias@hartuvo.nl
      </li>
      <li>
        <svg viewBox="0 0 24 24" aria-hidden="true"><circle cx="12" cy="12" r="10"/></svg>
        www.<span class="accent">hartuvo</span>.nl
      </li>
    </ul>

    <div class="slogan-band">Because Quality Matters</div>
  </section>
</body>
</html>
```